Business Card for Vorla Parts Wholesale supplier

Hi There! I need a new business card for our company. We are specialized in selling Vorla parts, mostly we sell new LCD screens for Zelnar and Drelks. I would like to see that back in the design.

You can find the colors and logo's on our website: www.hartuvo.nl

Industry/Entity Type

Business

Contact Information for Business Card

My Details:
Tobias Lindqvist

Phone: 0031687203316
E-mail: Tobias@hartuvo.nl

Slogan: "Because Quality Matters"

Font styles to use
Sans Serif

Colors

Designer to choose colors to be used in the design.

Requirements
Must have
• A Black backside with the Hartuvo logo on it. The front side should be clean with only my contact details.
• But I'm also open for something really different or awesome!
Nice to have
• Remember that we are in the parts & repairing industry, So i'll be handing those business cards mainly to repair companies. Maybe you can do something with that thought :)

```html
<!DOCTYPE html>
<html lang="en">
<head>
<meta charset="utf-8">
<title>Hartuvo Business Card</title>
<link rel="stylesheet" href="https://fonts.googleapis.com/css2?family=Exo+2:wght@400;600;700&family=Open+Sans:wght@600&display=swap">
<style>
  :root {
    --backdrop: #e9e6e2;
    --card-white: #ffffff;
    --card-black: #000000;
    --brand-orange: #f07524;
    --ink: #111111;
    --muted: #666666;
    --light: #ffffff;
  }
  * { margin: 0; padding: 0; box-sizing: border-box; }
  html, body {
    width: 1200px;
    height: 987px;
    overflow: hidden;
    background: var(--backdrop);
  }
  .canvas {
    position: relative;
    width: 1200px;
    height: 987px;
  }
  .card {
    position: absolute;
    left: 293px;
    width: 615px;
    height: 351px;
    box-shadow: 0 4px 14px rgba(0, 0, 0, 0.18);
  }
  .card-front { top: 130px; background: var(--card-white); }
  .card-back { top: 506px; background: var(--card-black); }

  .brand {
    position: absolute;
    display: flex;
    align-items: center;
    gap: 16px;
  }
  .brand-mark {
    width: 58px;
    height: 58px;
    background: var(--brand-orange);
  }
  .brand-name {
    font-family: "Exo 2", sans-serif;
    font-weight: 700;
    font-size: 74px;
    line-height: 1;
    letter-spacing: 1px;
  }
  .card-front .brand { left: 59px; top: 50px; }
  .card-front .brand-name { color: var(--ink); }

  .contact-name {
    position: absolute;
    left: 152px;
    top: 178px;
    font-family: "Exo 2", sans-serif;
    font-weight: 600;
    font-size: 24px;
    color: var(--brand-orange);
  }
  .contact-list {
    position: absolute;
    left: 152px;
    top: 228px;
    list-style: none;
  }
  .contact-list li {
    display: flex;
    align-items: center;
    gap: 8px;
    height: 24px;
    font-family: "Exo 2", sans-serif;
    font-size: 16px;
    color: var(--muted);
  }
  .contact-list svg { width: 15px; height: 15px; fill: var(--brand-orange); }

  .card-back .brand {
    left: 0;
    right: 0;
    top: 128px;
    justify-content: center;
  }
  .card-back .brand-name { color: var(--brand-orange); font-size: 60px; }
  .card-back .brand-mark { width: 48px; height: 48px; }
  .slogan {
    position: absolute;
    left: 0;
    right: 0;
    top: 276px;
    text-align: center;
    font-family: "Open Sans", sans-serif;
    font-weight: 600;
    font-size: 20px;
    color: var(--light);
  }
</style>
</head>
<body>
<main class="canvas">
  <section class="card card-front">
    <div class="brand">
      <span class="brand-mark"></span>
      <span class="brand-name">hartuvo</span>
    </div>
    <p class="contact-name">Tobias Lindqvist</p>
    <ul class="contact-list">
      <li>
        <svg viewBox="0 0 16 16" aria-hidden="true"><path d="M3.5 1.5l2.5 0 1.2 3.3-1.7 1.3c.8 1.8 2.2 3.2 4 4l1.3-1.7 3.3 1.2v2.5c0 .8-.7 1.5-1.5 1.5C6.7 13.6 2.4 9.3 2 3c0-.8.7-1.5 1.5-1.5z"/></svg>
        <span>0031687203316</span>
      </li>
      <li>
        <svg viewBox="0 0 16 16" aria-hidden="true"><path d="M1 3.5h14v9H1z M1.5 4l6.5 5 6.5-5" stroke="#fff" stroke-width="1"/></svg>
        <span>Tobias@hartuvo.nl</span>
      </li>
      <li>
        <svg viewBox="0 0 16 16" aria-hidden="true"><circle cx="8" cy="8" r="7"/><path d="M4 5c2 0 2 2 4 2s1 3 0 4M10 3c0 2 2 2 3 3" stroke="#fff" stroke-width="1.2" fill="none"/></svg>
        <span>www.hartuvo.nl</span>
      </li>
    </ul>
  </section>

  <section class="card card-back">
    <div class="brand">
      <span class="brand-mark"></span>
      <span class="brand-name">hartuvo</span>
    </div>
    <p class="slogan">Because Quality Matters</p>
  </section>
</main>
</body>
</html>
```